Coastline Premier Retreats Business Card Design

Design a business card for Coastline Premier Retreats. Look at the website for colors and reference. Card should have logo, name, title, office number, mobile number, email, URL and a tagline like, "Luxury Hotel & Resort Email Marketing" (This might change).

https://www.coastlinepremierretreats.example

The rest I will leave up to your imagination.

Contact Information for Business Card

Logo, name, title, office number, mobile number, email, URL and a tagline like, "Luxury Hotel & Resort Email Marketing" (This might change).

```html
<!DOCTYPE html>
<html lang="en">
<head>
<meta charset="utf-8">
<title>Coastline Premier Retreats – Business Card</title>
<link rel="stylesheet" href="https://fonts.googleapis.com/css2?family=Open+Sans:wght@400;600;700&display=swap">
<style>
  :root {
    --backdrop: #222222;
    --brand-orange: #f07321;
    --card-white: #fdfdf6;
    --ink: #111111;
    --on-orange: #ffffff;
  }
  * { box-sizing: border-box; margin: 0; padding: 0; }
  html, body { width: 1200px; height: 780px; overflow: hidden; }
  body {
    background: var(--backdrop);
    font-family: "Open Sans", Arial, sans-serif;
    position: relative;
  }
  .card {
    position: absolute;
    top: 230px;
    width: 560px;
    height: 320px;
    overflow: hidden;
  }
  .card--front { left: 20px; background: var(--card-white); }
  .card--back  { left: 620px; background: var(--brand-orange); }

  .front-curve { position: absolute; inset: 0; }

  .front-logo {
    position: absolute;
    left: 40px; top: 70px;
    width: 230px;
    font-weight: 700;
    font-size: 22px;
    line-height: 1.15;
    color: var(--ink);
    display: flex; align-items: center; gap: 10px;
  }
  .front-logo .logo-square {
    width: 14px; height: 14px; flex: none;
    background: var(--brand-orange);
  }
  .divider {
    position: absolute;
    left: 286px; top: 50px;
    width: 1px; height: 150px;
    background: var(--ink);
  }
  .person { position: absolute; left: 304px; top: 56px; }
  .person-name { font-size: 23px; font-weight: 700; color: var(--ink); line-height: 1.1; }
  .person-name .first { color: var(--brand-orange); }
  .person-title { font-size: 13px; margin-top: 2px; color: var(--ink); }
  .contacts { list-style: none; margin-top: 10px; }
  .contacts li {
    display: flex; align-items: center; gap: 7px;
    font-size: 12px; line-height: 19px; color: var(--ink);
  }
  .contacts svg { width: 11px; height: 11px; flex: none; fill: var(--brand-orange); }

  .tagline {
    position: absolute;
    left: 92px; top: 288px;
    font-size: 13px;
    line-height: 18px;
    white-space: nowrap;
    color: var(--on-orange);
  }

  .back-logo {
    position: absolute; inset: 0;
    display: flex; align-items: center; justify-content: center;
    font-weight: 700; font-size: 34px;
    color: var(--on-orange);
    text-align: center; line-height: 1.15;
    padding: 0 60px;
  }
</style>
</head>
<body>
  <section class="card card--front" aria-label="Business card front">
    <svg class="front-curve" viewBox="0 0 560 320" aria-hidden="true">
      <path d="M0 318 C 140 236, 360 236, 560 320 L0 320 Z" fill="var(--brand-orange)"/>
      <path d="M0 318 C 140 236, 360 236, 560 320" fill="none" stroke="#111111" stroke-width="4"/>
    </svg>

    <div class="front-logo"><span class="logo-square"></span><span>Coastline Premier Retreats</span></div>
    <div class="divider"></div>

    <div class="person">
      <p class="person-name"><span class="first">Marta</span> Vellinger</p>
      <p class="person-title">Co-Founder</p>
      <ul class="contacts">
        <li><svg viewBox="0 0 24 24"><path d="M6.6 10.8a15 15 0 0 0 6.6 6.6l2.2-2.2a1 1 0 0 1 1-.25 11 11 0 0 0 3.6.6 1 1 0 0 1 1 1V20a1 1 0 0 1-1 1A17 17 0 0 1 3 4a1 1 0 0 1 1-1h3.5a1 1 0 0 1 1 1 11 11 0 0 0 .6 3.6 1 1 0 0 1-.25 1z"/></svg>(555) 014-2758</li>
        <li><svg viewBox="0 0 24 24"><path d="M7 1h10a2 2 0 0 1 2 2v18a2 2 0 0 1-2 2H7a2 2 0 0 1-2-2V3a2 2 0 0 1 2-2zm0 3v14h10V4z"/></svg>(555) 019-7777</li>
        <li><svg viewBox="0 0 24 24"><circle cx="12" cy="12" r="10"/></svg>www.coastlinepremierretreats.example</li>
        <li><svg viewBox="0 0 24 24"><path d="M2 5h20v14H2zm2 2v.5l8 5 8-5V7z"/></svg>info@coastlinepremierretreats.example</li>
      </ul>
    </div>

    <p class="tagline">Luxury Hotel &amp; Resort Email Marketing</p>
  </section>

  <section class="card card--back" aria-label="Business card back">
    <div class="back-logo">Coastline Premier Retreats</div>
  </section>
</body>
</html>
```